Settlewell202.com flyer for window coverings

two sided 8 1/2 x 11 flyer featuring window coverings to send people to our website to shop for window coverings. Can use stock photos of blinds and shutters (wood toned blinds, white shutters, grey roller shades, white faux wood blinds). We don't sell draperies or drapery rods. We do sell other product like lighting and cabinet organization but we would like this flyer to focus on window coverings. We want to be a resource for new home buyers that need items to finish making their new house their home.

Target Market(s)

New home buyers

Industry/Entity Type

Real Estate

Font styles to use
Sans Serif

Requirements
Must have
• photos of window blinds and shades--photos have been added 3/31
• logo of settlewell202.com
• "Settlewell202.com - #1 - Cover your windows for: Privacy, Security, Energy Efficiency. We have all the styles to meet your needs and installation available!"
Should not have
• Pictures of towel bars

```html
<!DOCTYPE html>
<html lang="en">
<head>
<meta charset="utf-8">
<title>Settlewell202.com – Window Coverings Flyer</title>
<link href="https://fonts.googleapis.com/css2?family=Source+Sans+3:ital,wght@0,400;0,600;0,700;1,700&display=swap" rel="stylesheet">
<style>
  :root{
    --red:#d42027;
    --ink:#1d1d1d;
    --grey-bg:#d3d4d6;
    --paper:#ffffff;
    --wood-light:#e9c7a0;
    --wood:#b98350;
    --yellow:#ffe600;
  }
  *{box-sizing:border-box;margin:0;padding:0}
  html,body{width:1200px;height:775px;overflow:hidden;background:var(--grey-bg)}
  body{position:relative;font-family:"Source Sans 3",sans-serif;color:var(--ink)}
  .page{position:absolute;top:55px;width:498px;height:647px;background:var(--paper);overflow:hidden;box-shadow:0 6px 14px rgba(0,0,0,.18)}
  .page--front{left:44px}
  .page--back{left:646px}

  .brand{position:absolute;left:36px;top:34px;display:flex;align-items:center;gap:8px;z-index:3}
  .brand__dot{width:34px;height:34px;border-radius:50%;background:var(--red)}
  .brand__name{font-size:24px;font-weight:700;color:#3a3a3a;letter-spacing:-.3px}

  /* front */
  .front-photo{position:absolute;inset:0;background:linear-gradient(90deg,var(--paper) 0%,var(--paper) 62%,#f3e2cf 70%,var(--wood-light) 80%,var(--wood) 100%)}
  .front-copy{position:absolute;left:25px;top:0;width:440px;z-index:2}
  .tagline{position:absolute;top:164px;font-size:19.8px;font-weight:600;white-space:nowrap}
  .tagline em{font-style:normal;color:var(--red)}
  .site-caps{position:absolute;top:188px;font-size:18px;font-weight:700;letter-spacing:.2px}
  .small{font-size:12.3px;line-height:15px;white-space:nowrap}
  .small .hl{color:var(--red);font-weight:600}
  .styles{position:absolute;top:232px}
  .install{position:absolute;top:249px;font-size:20px;font-weight:600;color:var(--red);white-space:nowrap}
  .cover{position:absolute;top:284px}
  .shop{position:absolute;top:329px;line-height:18px}
  .shop .code{color:var(--red);font-weight:700;font-style:italic;font-size:14.5px}
  .phone{position:absolute;top:392px;left:0;width:324px;height:55px;border-radius:27px;background:var(--red);color:#fff;font-size:26px;display:flex;align-items:center;justify-content:center;gap:10px}
  .phone strong{font-weight:600}
  .visit{position:absolute;top:467px;font-size:11px;white-space:nowrap}
  .visit a{color:var(--red);font-weight:700;font-size:21px;text-decoration:none}
  .live{position:absolute;top:487px;font-size:11.5px;line-height:15px;white-space:nowrap}

  /* back */
  .back-photo{position:absolute;inset:0;background:linear-gradient(100deg,#ffffff 0%,#f6f6f6 45%,#ececec 75%,#e2e2e2 100%)}
  .circles{position:absolute;left:0;top:0}
  .offer{position:absolute;left:22px;top:252px;color:#fff;font-size:12.3px;line-height:15.8px;white-space:nowrap}
  .offer p+p{margin-top:15.6px}
  .offer .deal{color:var(--yellow);font-weight:700}
  .gallery{position:absolute;left:308px;top:31px;width:190px;height:587px;border:3px solid var(--red);border-right:none;display:flex;flex-direction:column;gap:3px;background:var(--red)}
  .gallery__item{flex:1}
  .gallery__item--roller{background:linear-gradient(180deg,#efe9dc 0%,#e2dccb 55%,#b9a98a 100%)}
  .gallery__item--shutter{background:linear-gradient(180deg,#f6f4f0 0%,#d9d3ca 60%,#8d857a 100%)}
  .gallery__item--vertical{background:linear-gradient(180deg,#f4f4f1 0%,#e3e3dc 60%,#b8b49a 100%)}
  .back-footer{position:absolute;left:22px;top:625px;font-size:10.9px;white-space:nowrap}
  .back-footer a{color:var(--red);font-weight:700;text-decoration:none}
</style>
</head>
<body>

<section class="page page--front">
  <div class="front-photo" role="img" aria-label="Hand pulling the wand of wood-toned window blinds"></div>
  <div class="brand"><span class="brand__dot"></span><span class="brand__name">Settlewell 202</span></div>
  <div class="front-copy">
    <p class="tagline"><em>Free Shipping</em> and <em>No Minimums!</em></p>
    <p class="site-caps">SETTLEWELL202.COM</p>
    <p class="small styles">We have all the styles to meet your needs.</p>
    <p class="install">INSTALLATION OPTIONS ARE AVAILABLE!</p>
    <p class="small cover">Cover your windows for: <span class="hl">Privacy, Security, Energy Efficiency.</span><br>We have all the styles to meet your needs and installation available!</p>
    <p class="small shop">Go to <span class="hl">www.settlewell202.com</span> to shop for your home and<br>during checkout enter your promo <span class="code">code WEL10</span> for your discount.</p>
    <div class="phone">Phone: <strong>555-014-2290</strong></div>
    <p class="visit">Visit us at: <a href="#">www.settlewell202.com</a></p>
    <p class="live">Live chat available to answer any questions you might have.</p>
  </div>
</section>

<section class="page page--back">
  <div class="back-photo" role="img" aria-label="Soft light through white faux wood blinds"></div>
  <svg class="circles" width="498" height="647" viewBox="0 0 498 647" aria-hidden="true">
    <circle cx="71" cy="370" r="203" fill="#dcdcdc" opacity=".85"/>
    <circle cx="53" cy="369" r="179" fill="#d42027"/>
  </svg>
  <div class="brand"><span class="brand__dot"></span><span class="brand__name">Settlewell 202</span></div>
  <div class="offer">
    <p>Your builder and their<br>supplier have partnered<br>together to offer you this<br>special <span class="deal">10% discount</span> on a<br>wide variety of window blinds<br>and shades along with other<br>products to finish making<br>your house your home.</p>
    <p>We offer faux wood blinds,<br>roller shades, verticals, faux<br>wood shutters, sliding panels<br>and honey comb shades in a<br>variety of colors and finishes.</p>
  </div>
  <div class="gallery">
    <div class="gallery__item gallery__item--roller" role="img" aria-label="Kitchen window with a pale roller shade"></div>
    <div class="gallery__item gallery__item--shutter" role="img" aria-label="Arched window fitted with white shutters"></div>
    <div class="gallery__item gallery__item--vertical" role="img" aria-label="Living room with white vertical blinds"></div>
  </div>
  <p class="back-footer">Visit us at: <a href="#">www.settlewell202.com.</a>&nbsp; Live chat available to answer any questions you might have.</p>
</section>

</body>
</html>
```